Harbourline Electrical Solutions

On one side. LOGO (underneath:) Commercial Industrial Residential

- NAME & CONTACT DETAILS

Marcus T. Hollings
Project Manager

(Cell icon) (441) 555-0187
(Email icon) hlelectricalsolutions@mailvento.com
(Facebook & Instagram icons )@hlelectricalsolutions

Other side: LOGO - underneath ELECTRICAL CONSTRUCTION & MAINTENANCE . LED LIGHTING & AUTOMATION . LIFE SAFETY SYSTEMS (FIRE ALARM / SECURITY) . DATA & COMMUNICATION

```html
<!DOCTYPE html>
<html lang="en">
<head>
<meta charset="UTF-8">
<title>Harbourline Electrical Solutions – Business Card</title>
<link href="https://fonts.googleapis.com/css2?family=Montserrat:ital,wght@0,400;0,500;0,600;0,700;1,400&family=Poppins:wght@400;500&display=swap" rel="stylesheet">
<style>
  :root {
    --teal: #0f5068;
    --teal-deep: #0b4257;
    --ink: #3a3a3a;
    --grey: #5a5a5a;
    --paper: #ffffff;
    --backdrop: #e6eaec;
  }
  * { box-sizing: border-box; margin: 0; padding: 0; }
  html, body { width: 1200px; height: 900px; overflow: hidden; }
  body {
    background: var(--backdrop);
    font-family: "Montserrat", sans-serif;
    position: relative;
  }
  .card {
    position: absolute;
    left: 250px;
    width: 700px;
    height: 400px;
    box-shadow: 0 6px 18px rgba(0,0,0,0.12);
    overflow: hidden;
  }
  /* ---------- Front ---------- */
  .card--front { top: 30px; background: var(--paper); }
  .front__accent {
    position: absolute; left: 0; bottom: 0;
    width: 14px; height: 110px; background: var(--teal);
  }
  .brand {
    position: absolute; left: 70px; top: 60px;
    display: flex; align-items: center; gap: 22px;
  }
  .brand__square { width: 64px; height: 64px; background: var(--teal); flex: none; }
  .brand__rule { width: 2px; height: 100px; background: var(--ink); flex: none; }
  .brand__name {
    font-weight: 600; font-size: 25px; line-height: 1.08;
    letter-spacing: 3px; text-transform: uppercase; color: var(--teal);
  }
  .brand__tagline {
    margin-top: 8px; font-family: "Poppins", sans-serif; font-size: 17px;
    color: var(--ink); letter-spacing: 0.3px;
  }
  .person { position: absolute; left: 70px; top: 215px; }
  .person__name {
    font-weight: 700; font-size: 25px; color: var(--teal);
    text-transform: uppercase; letter-spacing: 0.5px;
  }
  .person__role { font-family: "Poppins", sans-serif; font-size: 18px; color: var(--ink); margin-top: 2px; }
  .contacts { list-style: none; margin-top: 18px; font-family: "Poppins", sans-serif; font-size: 16px; color: var(--ink); }
  .contacts li { display: flex; align-items: center; gap: 10px; margin-bottom: 6px; }
  .contacts .icon { width: 20px; height: 20px; flex: none; }
  .social-dot { width: 20px; height: 20px; border-radius: 50%; background: var(--teal); flex: none; }
  /* ---------- Back ---------- */
  .card--back {
    top: 470px;
    background: linear-gradient(160deg, var(--teal) 0%, var(--teal-deep) 100%);
    color: #fff;
  }
  .back__brand {
    position: absolute; left: 0; right: 0; top: 105px;
    display: flex; justify-content: center; align-items: center; gap: 22px;
  }
  .back__brand .brand__square { background: #fff; }
  .back__brand .brand__rule { background: #fff; }
  .back__brand .brand__name { color: #fff; }
  .services {
    position: absolute; left: 0; right: 0; top: 268px;
    text-align: center; font-size: 14px; font-weight: 500;
    letter-spacing: 1px; line-height: 1.7; text-transform: uppercase;
  }
</style>
</head>
<body>

<section class="card card--front" aria-label="Business card front">
  <div class="brand">
    <span class="brand__square" aria-hidden="true"></span>
    <span class="brand__rule" aria-hidden="true"></span>
    <div>
      <div class="brand__name">Harbourline<br>Electrical<br>Solutions</div>
      <div class="brand__tagline">Commercial Industrial Residential</div>
    </div>
  </div>

  <div class="person">
    <div class="person__name">Marcus T. Hollings</div>
    <div class="person__role">Project Manager</div>
    <ul class="contacts">
      <li>
        <svg class="icon" viewBox="0 0 20 20" aria-hidden="true">
          <circle cx="10" cy="10" r="10" fill="#0f5068"/>
          <rect x="7" y="4.5" width="6" height="11" rx="1.2" fill="#fff"/>
          <rect x="8" y="6" width="4" height="7" fill="#0f5068"/>
        </svg>
        (441) 555-0187
      </li>
      <li>
        <svg class="icon" viewBox="0 0 20 20" aria-hidden="true">
          <circle cx="10" cy="10" r="10" fill="#0f5068"/>
          <rect x="5" y="6.5" width="10" height="7" fill="#fff"/>
          <polyline points="5,6.5 10,10.5 15,6.5" fill="none" stroke="#0f5068" stroke-width="1.2"/>
        </svg>
        hlelectricalsolutions@mailvento.com
      </li>
      <li>
        <span class="social-dot" aria-hidden="true"></span>
        <span class="social-dot" aria-hidden="true"></span>
        @hlelectricalsolutions
      </li>
    </ul>
  </div>
  <span class="front__accent" aria-hidden="true"></span>
</section>

<section class="card card--back" aria-label="Business card back">
  <div class="back__brand">
    <span class="brand__square" aria-hidden="true"></span>
    <span class="brand__rule" aria-hidden="true"></span>
    <div class="brand__name">Harbourline<br>Electrical<br>Solutions</div>
  </div>
  <p class="services">
    Electrical Construction &amp; Maintenance | LED Lighting &amp; Automation<br>
    Life Safety Systems (Fire Alarm / Security) | Data &amp; Communication
  </p>
</section>

</body>
</html>
```